Local Roofing/Construction company business needs new biz card design

We need a new business card design, current cards are from the start of this operation and generic at best. We are a local Construction Company (General Contractor) with a majority of our work originating from insurance claims-exterior finish work is the main focus (Roofs-Siding-Gutters etc). Heavily involved with homeowners and the low ball offers they receive from insurance company's after a insurable event takes place. I have attached some of our original logo file(s) below.

```html
<!DOCTYPE html>
<html lang="en">
<head>
<meta charset="utf-8">
<title>Ridgeway Builders – Business Card</title>
<link href="https://fonts.googleapis.com/css2?family=Montserrat:wght@400;500;700;800&display=swap" rel="stylesheet">
<style>
  :root {
    --bg: #3a3a3a;
    --ink: #031a20;
    --ink-deep: #01141a;
    --green: #00d67a;
    --paper: #ffffff;
    --divider: #4a5a60;
  }
  * { box-sizing: border-box; margin: 0; padding: 0; }
  html, body { width: 1200px; height: 1200px; overflow: hidden; }
  body {
    background: var(--bg);
    font-family: "Montserrat", Arial, sans-serif;
    position: relative;
  }
  .card {
    position: absolute;
    left: 160px;
    width: 880px;
    height: 503px;
    border-radius: 40px;
    overflow: hidden;
  }
  .card-front { top: 70px; background: var(--ink); }
  .card-back  { top: 627px; background: radial-gradient(circle at 50% 40%, #06252c, var(--ink-deep) 75%); }

  .front-top {
    position: absolute; left: 0; top: 0; width: 100%; height: 262px;
    background: var(--paper);
  }
  .front-stripe {
    position: absolute; left: 0; top: 262px; width: 100%; height: 10px;
    background: var(--green);
  }
  .brand {
    position: absolute; left: 0; right: 0; top: 100px;
    display: flex; align-items: center; justify-content: center; gap: 18px;
  }
  .brand-square { width: 46px; height: 46px; background: var(--green); }
  .brand-name {
    font-weight: 800; font-size: 50px; letter-spacing: 1px;
    color: var(--ink); text-transform: uppercase;
  }

  .person {
    position: absolute; left: 90px; top: 355px;
  }
  .person-name {
    color: var(--green); font-weight: 500; font-size: 40px; line-height: 1;
    letter-spacing: 0.5px;
  }
  .person-role {
    color: var(--paper); font-weight: 400; font-size: 22px; margin-top: 4px;
    letter-spacing: 0.5px;
  }
  .front-divider {
    position: absolute; left: 455px; top: 300px; width: 1.5px; height: 165px;
    background: var(--divider);
  }
  .contact {
    position: absolute; left: 500px; top: 306px;
    list-style: none; color: var(--paper); font-size: 19px; line-height: 1.3;
  }
  .contact li { display: flex; align-items: flex-start; gap: 12px; margin-bottom: 4px; }
  .contact svg { width: 20px; height: 20px; flex: none; margin-top: 2px; }

  .back-brand {
    position: absolute; inset: 0;
    display: flex; align-items: center; justify-content: center; gap: 22px;
  }
  .back-brand .brand-square { width: 70px; height: 70px; }
  .back-brand .brand-name { color: var(--green); font-size: 64px; }
</style>
</head>
<body>

<section class="card card-front">
  <div class="front-top"></div>
  <div class="front-stripe"></div>
  <div class="brand">
    <span class="brand-square"></span>
    <span class="brand-name">Ridgeway Builders</span>
  </div>

  <div class="person">
    <p class="person-name">FULL NAME</p>
    <p class="person-role">POSITION</p>
  </div>

  <div class="front-divider"></div>

  <ul class="contact">
    <li>
      <svg viewBox="0 0 24 24" aria-hidden="true"><path fill="#00d67a" d="M6.6 10.8a15.1 15.1 0 0 0 6.6 6.6l2.2-2.2c.3-.3.7-.4 1-.2 1.1.4 2.3.6 3.6.6.6 0 1 .4 1 1V20c0 .6-.4 1-1 1A17 17 0 0 1 3 4c0-.6.4-1 1-1h3.5c.6 0 1 .4 1 1 0 1.2.2 2.4.6 3.6.1.3 0 .7-.2 1z"/></svg>
      <span>555-014-2290</span>
    </li>
    <li>
      <svg viewBox="0 0 24 24" aria-hidden="true"><g fill="none" stroke="#00d67a" stroke-width="2"><circle cx="12" cy="12" r="9"/><path d="M3 12h18M12 3c3 3 3 15 0 18M12 3c-3 3-3 15 0 18"/></g></svg>
      <span>www.ridgewaybuilders.com</span>
    </li>
    <li>
      <svg viewBox="0 0 24 24" aria-hidden="true"><g fill="none" stroke="#00d67a" stroke-width="2"><rect x="3" y="5" width="18" height="14"/><path d="M3 5l9 8 9-8"/></g></svg>
      <span>office@ridgewaybuilders.com</span>
    </li>
    <li>
      <svg viewBox="0 0 24 24" aria-hidden="true"><path fill="#00d67a" d="M12 2a7 7 0 0 0-7 7c0 5 7 13 7 13s7-8 7-13a7 7 0 0 0-7-7zm0 9.5a2.5 2.5 0 1 1 0-5 2.5 2.5 0 0 1 0 5z"/></svg>
      <span>42 Oak Hollow Ln<br>Fairview, MO 63000</span>
    </li>
  </ul>
</section>

<section class="card card-back">
  <div class="back-brand">
    <span class="brand-square"></span>
    <span class="brand-name">Ridgeway Builders</span>
  </div>
</section>

</body>
</html>
```